TalkHarbor - Language Coaching Services

Sleek, innovative, trendy design for Language Coaching business.

TalkHarbor is a new UK based company that provides Language Coaching services. We offer highly personalized on-line and face to face language courses. We also impart learning techniques workshops based on the latest neuroscience research for second-language acquisition.

Target Market(s)

See attached info

Industry/Entity Type

Consulting

Contact Information for Business Card

TalkHarbor
DaniaKV@talkharbor.co.uk
TalkHarbor.co.uk
London, UK

Font styles to use
Sans Serif

```html
<!DOCTYPE html>
<html lang="en">
<head>
<meta charset="utf-8">
<title>TalkHarbor Business Card</title>
<link rel="stylesheet" href="https://fonts.googleapis.com/css2?family=Montserrat:wght@300&family=Oswald:wght@500&family=PT+Sans&display=swap">
<style>
  :root {
    --backdrop: #2b2b2b;
    --card: #222222;
    --silver: #c9c9c9;
    --brand-blue: #1f8fbf;
    --accent-blue: #5b86d6;
    --text-light: #eeeeee;
  }
  * { margin: 0; padding: 0; box-sizing: border-box; }
  html, body { width: 1200px; height: 1200px; overflow: hidden; background: var(--backdrop); }
  .sheet { position: relative; width: 1200px; height: 1200px; }
  .card {
    position: absolute; left: 120px; width: 960px; height: 548px;
    background: var(--card);
    box-shadow: 0 12px 30px rgba(0,0,0,.45);
  }
  .card--front { top: 40px; }
  .card--back { top: 612px; }

  .brand { display: flex; flex-direction: column; align-items: center; position: absolute; }
  .brand__mark { width: 150px; height: 150px; border-radius: 50%; border: 9px solid currentColor; }
  .brand__name {
    font-family: "Montserrat", sans-serif; font-weight: 300;
    font-size: 64px; letter-spacing: 4px; margin-top: 22px;
  }
  .card--front .brand { color: var(--silver); left: 0; right: 0; top: 120px; }
  .card--back .brand { color: var(--brand-blue); left: 40px; width: 480px; top: 120px; }
  .card--back .brand__name { font-size: 54px; letter-spacing: 3px; }

  .divider {
    position: absolute; left: 560px; top: 130px; width: 2px; height: 290px;
    background: linear-gradient(to bottom, transparent, var(--accent-blue), transparent);
  }
  .contact { position: absolute; left: 610px; top: 150px; font-family: "PT Sans", sans-serif; color: var(--text-light); }
  .contact__name { font-family: "Oswald", sans-serif; font-weight: 500; font-size: 40px; color: var(--accent-blue); letter-spacing: 1px; line-height: 1.1; }
  .contact__role { font-size: 21px; letter-spacing: 1px; margin-bottom: 16px; }
  .contact__address { font-size: 21px; line-height: 1.3; letter-spacing: .5px; margin-bottom: 16px; }
  .contact__list { list-style: none; font-size: 21px; line-height: 1.45; }
  .contact__list li { display: flex; align-items: center; gap: 14px; }
  .contact__icon { width: 18px; height: 18px; fill: var(--accent-blue); flex: none; }
</style>
</head>
<body>
<div class="sheet">
  <section class="card card--front">
    <div class="brand">
      <div class="brand__mark"></div>
      <div class="brand__name">TALKHARBOR</div>
    </div>
  </section>

  <section class="card card--back">
    <div class="brand">
      <div class="brand__mark"></div>
      <div class="brand__name">TALKHARBOR</div>
    </div>
    <div class="divider"></div>
    <div class="contact">
      <div class="contact__name">ELLIS HARTLEY</div>
      <div class="contact__role">President &amp; CEO</div>
      <div class="contact__address">Quayside Partners, LLP 18<br>Harbour Row, Ste 4 London</div>
      <ul class="contact__list">
        <li>
          <svg class="contact__icon" viewBox="0 0 24 24"><path d="M6.6 10.8a15 15 0 0 0 6.6 6.6l2.2-2.2a1 1 0 0 1 1-.25 11.4 11.4 0 0 0 3.6.57 1 1 0 0 1 1 1V20a1 1 0 0 1-1 1A17 17 0 0 1 3 4a1 1 0 0 1 1-1h3.5a1 1 0 0 1 1 1c0 1.25.2 2.45.57 3.57a1 1 0 0 1-.25 1z"/></svg>
          +(000) -000- 0000
        </li>
        <li>
          <svg class="contact__icon" viewBox="0 0 24 24"><path d="M2 5h20v14H2z M2 5l10 8 10-8" fill="none" stroke="#5b86d6" stroke-width="2"/></svg>
          info@talkharbor.co.uk
        </li>
        <li>
          <svg class="contact__icon" viewBox="0 0 24 24"><circle cx="12" cy="12" r="9" fill="none" stroke="#5b86d6" stroke-width="2"/><path d="M3 12h18M12 3c3 3 3 15 0 18M12 3c-3 3-3 15 0 18" fill="none" stroke="#5b86d6" stroke-width="1.5"/></svg>
          www.talkharbor.co.uk
        </li>
      </ul>
    </div>
  </section>
</div>
</body>
</html>
```